Quorva - corporate Business Card

We need a good look and innovative business card for a new start up company based in Los Angeles called "Quorva". We are in a payment business, including payment card, app, and ewallet. We are expert in online payment and Card not present (CNP) transaction.
We need an innovative, modern business card.

Our logo font is Aero Matics

Target Market(s)

Startup - Bank - Online Payment - Card Manufacturing

Industry/Entity Type

Startup

Contact Information for Business Card

phone: 555 014 7396 - Address: 4172 Marlowe blvd, Dunmere Heights, CA 90299

Requirements
Must have
• Message: innovative, professional, expert, high tech, trust, online payment expert, security
Nice to have
• no comment
Should not have
• no Comment

```html
<!DOCTYPE html>
<html lang="en">
<head>
<meta charset="utf-8">
<title>Quorva Business Card</title>
<link rel="stylesheet" href="https://fonts.googleapis.com/css2?family=Open+Sans:wght@400;700&display=swap">
<style>
  :root {
    --backdrop: #222222;
    --brand-red: #b5202f;
    --paper: #ffffff;
    --blush: #f5e3dd;
    --muted: #8f8f8f;
  }
  * { margin: 0; padding: 0; box-sizing: border-box; }
  html, body {
    width: 1189px; height: 1200px; overflow: hidden;
    background: var(--backdrop);
    font-family: "Open Sans", Arial, sans-serif;
  }
  .card {
    position: absolute; left: 171px; width: 856px; height: 488px;
    overflow: hidden;
    box-shadow: 2px 3px 6px rgba(0,0,0,.6);
  }
  .card--front { top: 67px; background: var(--brand-red); }
  .card--back { top: 625px; background: var(--paper); }

  .brand-dot { position: absolute; border-radius: 50%; }
  .brand-name {
    position: absolute; font-weight: 700; line-height: 1; letter-spacing: -1px;
    text-transform: lowercase;
  }
  .card--front .brand-dot { left: 188px; top: 172px; width: 146px; height: 146px; background: var(--paper); }
  .card--front .brand-name { left: 350px; top: 180px; font-size: 98px; color: var(--paper); }

  .tab { position: absolute; left: 52px; top: 0; width: 125px; height: 77px; background: var(--brand-red); }
  .tab-ring { position: absolute; left: 36px; top: 51px; width: 166px; height: 166px; border-radius: 50%; background: var(--paper); }
  .card--back .brand-dot { left: 51px; top: 66px; width: 136px; height: 136px; background: var(--brand-red); }
  .card--back .brand-name { left: 202px; top: 94px; font-size: 86px; color: var(--brand-red); }

  .backdrop-circle { position: absolute; left: 587px; top: -30px; width: 360px; height: 360px; border-radius: 50%; background: var(--blush); }

  .person { position: absolute; left: 48px; top: 290px; }
  .person-name { font-size: 29px; font-weight: 700; color: var(--brand-red); line-height: 32px; }
  .person-role { font-size: 23px; color: var(--muted); line-height: 22px; }

  .contacts { position: absolute; left: 48px; top: 402px; list-style: none; }
  .contacts li { display: flex; align-items: center; gap: 14px; font-size: 21px; color: var(--muted); line-height: 29px; }
  .contacts svg { width: 22px; height: 22px; flex: none; }

  .address { position: absolute; right: 36px; top: 403px; text-align: right; font-style: normal; font-size: 21px; color: var(--muted); line-height: 28px; }
</style>
</head>
<body>
  <section class="card card--front">
    <span class="brand-dot"></span>
    <span class="brand-name">quorva</span>
  </section>

  <section class="card card--back">
    <span class="backdrop-circle"></span>
    <span class="tab"></span>
    <span class="tab-ring"></span>
    <span class="brand-dot"></span>
    <span class="brand-name">quorva</span>

    <div class="person">
      <p class="person-name">Daniel Reyes</p>
      <p class="person-role">Managing Director</p>
    </div>

    <ul class="contacts">
      <li>
        <svg viewBox="0 0 24 24" aria-hidden="true"><circle cx="12" cy="12" r="12" fill="#b5202f"/><path d="M6 10c0-2 3-3 6-3s6 1 6 3v1h-3v-1.5H9V11H6z M8 12h8l1 5H7z" fill="#fff"/><circle cx="12" cy="14.5" r="1.4" fill="#b5202f"/></svg>
        <span>555 014 7396</span>
      </li>
      <li>
        <svg viewBox="0 0 24 24" aria-hidden="true"><circle cx="12" cy="12" r="12" fill="#b5202f"/><rect x="6" y="8" width="12" height="8" fill="none" stroke="#fff" stroke-width="1.5"/><path d="M6 8l6 5 6-5M6 16l4.5-4M18 16l-4.5-4" fill="none" stroke="#fff" stroke-width="1.5"/></svg>
        <span>hello@quorvapay.com</span>
      </li>
    </ul>

    <address class="address">4172 Marlowe blvd,<br>Dunmere Heights, CA 90299</address>
  </section>
</body>
</html>
```